CalmPeak Nurses' Manifesto

Design a manifesto to inspire and motivate nurses to work at minimum standards of excellence in their nursing practice.

The manifesto will become a feature of our website, at conferences, workshops and retreats. It will also be featured on other marketing tools.

Primary Market:
Nurses and/or other healthcare professionals (specifically Doctors, Occupational Therapists, Psychologists and Social Workers).

However the manifesto is equally applicable to all nurses and healthcare professionals from new graduates to very experienced senior clinicians, administration officers,managers and healthcare executive personnel.

Mainly females and primarily 35 to 65 years old, which suggests people in this target age group have extensive experience, but have become jaded'.

The purpose of our business is to assist healthcare professionals, primarily nurses, to maintain their enthusiasm and excellence in service provision, for their benefit as well as the benefit of the clients.

I have attached:
File 1: Copy Samples and examples: which has the copy for the manifesto, examples that appeal to us and our 3 attempts.
File 2: Our colour Spec Sheet, HOWEVER the colours are not necessary limited to these colours. These colours are not in the logo that will be on the manifesto. The colours on the logo attached can/or also be used.
File 3: Prototype logo. The final logo will be available within 3 to 4 days.

Industry/Entity Type

Healthcare

Requirements
Must have
• Must use the copy as per the attached file.

It should be contemporary, eye catching and motivational.

Should not have
• MUST BE EASY TO READ. Each line MUST be clearly defined from each other.

```html
<!DOCTYPE html>
<html lang="en">
<head>
<meta charset="utf-8">
<title>CalmPeak Nurses' Manifesto</title>
<link rel="stylesheet" href="https://fonts.googleapis.com/css2?family=Cabin:wght@400;600&family=Signika:wght@500;600&family=Libre+Baskerville:wght@400;700&family=Pinyon+Script&family=Fredoka:wght@600;700&family=Bungee&family=Russo+One&family=Quicksand:wght@400&family=Courier+Prime:wght@400;700&family=Bitter:wght@800&family=Federant&family=Dancing+Script:wght@400&family=Oswald:wght@400;700&display=swap">
<style>
:root{
  --page:#e7e4df;
  --slate:#3f5a58;
  --white:#ffffff;
  --lime:#a4cf4c;
  --orange:#f29a4c;
  --grey:#a9a9a9;
  --green:#3ea95a;
  --teal:#4fb3aa;
}
html,body{margin:0;width:1200px;height:1181px;overflow:hidden;background:var(--page);}
.manifesto{position:absolute;left:218px;top:78px;width:764px;height:1015px;background:var(--slate);overflow:hidden;}
.line{position:absolute;margin:0;white-space:nowrap;line-height:1.15;}
.vertical-up{writing-mode:vertical-rl;transform:rotate(180deg);}
.vertical-down{writing-mode:vertical-rl;}

.deliver-care{left:26px;top:32px;font:700 38px/1.1 "Oswald",sans-serif;color:var(--green);}
.smile{left:20px;top:442px;font:400 22px/1.35 "Libre Baskerville",serif;color:var(--white);}
.always-be{left:12px;top:786px;height:205px;font:400 34px/1 "Cabin",sans-serif;color:var(--grey);letter-spacing:1px;}
.always-be small{display:block;font-size:20px;line-height:1.3;margin-left:6px;letter-spacing:0;}
.look-after{left:716px;top:16px;height:970px;font:400 21px/1 "Libre Baskerville",serif;color:var(--white);text-align:end;}
.respect-limits{left:600px;top:127px;font:400 41px/1.3 "Dancing Script",cursive;color:var(--teal);}

.nurse-with{left:93px;top:20px;font:400 35px "Cabin",sans-serif;color:var(--white);}
.delight{left:90px;top:66px;font:600 33px/43px "Signika",sans-serif;color:var(--lime);}
.learn{left:90px;top:150px;font:700 70px/1 "Libre Baskerville",serif;color:var(--grey);}
.support{left:325px;top:165px;font:400 19px/1.3 "Libre Baskerville",serif;color:var(--orange);}
.something-new{left:90px;top:228px;font:400 32px/1.35 "Libre Baskerville",serif;color:var(--grey);}
.learn-bar{position:absolute;left:174px;top:287px;width:232px;height:14px;background:var(--grey);}
.nurse-figure{position:absolute;left:427px;top:222px;width:170px;height:220px;border-radius:70px 70px 0 0;background:linear-gradient(180deg,#f4f4f2,#dfe3e1);}
.trust{left:90px;top:320px;font:400 38px/35px "Pinyon Script",cursive;color:var(--lime);}
.lifelong{left:86px;top:438px;font:700 58px/1 "Fredoka",sans-serif;color:var(--orange);}
.celebrate{left:85px;top:497px;font:400 24px/25px "Bungee",sans-serif;color:var(--green);letter-spacing:2px;}
.you-are{left:85px;top:552px;font:400 19px/1 "Russo One",sans-serif;color:var(--teal);}
.you-are b{font-weight:400;font-size:28px;}
.right-thing{left:301px;top:548px;font:400 25px "Cabin",sans-serif;color:var(--white);}
.exception{left:410px;top:568px;font:400 60px/1.1 "Cabin",sans-serif;color:var(--white);}
.revel{left:85px;top:598px;font:400 18px "Russo One",sans-serif;color:var(--teal);}
.seek-success{left:86px;top:620px;font:400 39px "Quicksand",sans-serif;color:var(--lime);}
.follow-leaders{left:86px;top:666px;font:700 15px "Courier Prime",monospace;color:var(--teal);}
.lead-with{left:88px;top:685px;font:400 22px "Cabin",sans-serif;color:var(--orange);}
.no-one{left:434px;top:666px;font:400 16px/1.35 "Courier Prime",monospace;color:var(--green);text-align:right;}
.lead{left:538px;top:712px;font:400 31px "Courier Prime",monospace;color:var(--green);}
.purpose{left:88px;top:716px;font:400 22px "Cabin",sans-serif;color:var(--orange);}
.respond{left:90px;top:746px;font:800 25px/29px "Bitter",serif;color:var(--white);}
.adopt{left:92px;top:834px;font:400 22px "Cabin",sans-serif;color:var(--lime);}
.choose{left:92px;top:860px;font:400 22px/1.6 "Courier Prime",monospace;color:var(--teal);letter-spacing:1px;}
.live-dream{left:94px;top:920px;font:400 60px/1 "Federant",serif;color:var(--orange);}
.brand{position:absolute;left:572px;top:946px;display:flex;align-items:center;gap:6px;font:600 15px/1.1 "Cabin",sans-serif;color:var(--white);}
.brand-dot{width:26px;height:26px;border-radius:50%;background:var(--teal);}
.rules{position:absolute;left:0;top:0;}
</style>
</head>
<body>
<main class="manifesto">
  <svg class="rules" width="764" height="1015" aria-hidden="true">
    <polygon points="297,663 417,663 417,707 297,707 297,692 397,692 397,663" fill="#f29a4c"/>
    <rect x="212" y="819" width="440" height="3" fill="#ffffff"/>
    <polygon points="500,864 648,864 648,878 520,878 520,915 457,915 457,902 500,902" fill="#f29a4c"/>
    <rect x="500" y="864" width="18" height="51" fill="#f29a4c"/>
  </svg>

  <p class="line vertical-up deliver-care">Delivercare skillfully.</p>
  <p class="line vertical-down smile">Smile and infect others with<br>your happiness and have fun!</p>
  <p class="line vertical-up always-be">Always be<small>solution focused.</small></p>
  <p class="line vertical-up look-after">Lookafter yourself&nbsp; and value your health as much as you value the health of others.</p>
  <p class="line vertical-down respect-limits">Respect the limits of people's knowledge and share your<br>knowledge generously.</p>

  <p class="line nurse-with">Nurse with open hands, hearts and minds.</p>
  <p class="line delight">Delight your clients and colleagues by<br>exceeding their expectations.</p>
  <p class="line learn">Learn</p>
  <p class="line support">Support your colleagues and<br>champion their purpose.</p>
  <p class="line something-new">something new each<br>day.</p>
  <div class="learn-bar"></div>
  <div class="nurse-figure" role="img" aria-label="White silhouette of a nurse in a cap holding a syringe"></div>
  <p class="line trust">Trust your knowledge<br>and seek advice only<br>from respected sources.</p>
  <p class="line lifelong">Be a life long learner.</p>
  <p class="line celebrate">Celebrate,respect and value the<br>diversity of australian culture.</p>
  <p class="line you-are">YOU ARE <b>UNIQUE,</b></p>
  <p class="line right-thing">Always do the right thing without</p>
  <p class="line exception">exception</p>
  <p class="line revel">REVEL IN YOUR INDIVIDUALITY.</p>
  <p class="line seek-success">Seek success firstly from within.</p>
  <p class="line follow-leaders">Only follow exceptional leaders.</p>
  <p class="line lead-with">Always lead with</p>
  <p class="line no-one">If there is no one<br>left to follow, then</p>
  <p class="line lead">lead!</p>
  <p class="line purpose">purpose,passion and commitment.</p>
  <p class="line respond">Respond to complex situations innovatively,<br>creatively and safely within the scope of your<br>practice.</p>
  <p class="line adopt">Adopt a'can do' attitude to everything that comes your way.</p>
  <p class="line choose">CHOOSE YOUR THOUGHTS WISELY,<br>THEY CREATE YOUR REALITY.</p>
  <p class="line live-dream">Live your dream.</p>
  <div class="brand"><span class="brand-dot"></span><span>CalmPeak<br>For Nurses</span></div>
</main>
</body>
</html>
```